Equipment Finance Specialist I work with companies who need the funds to buy their equipment

I would like a business card that stands out on the shelves. I want to be able to hand it to someone and say WOW. This card should have my logo.
You can put color into it I am very open on design and color

What my company does is we deal with dealerships that sell equipment such as Dump Trucks garbage trucks tractors trailers. Customers get referred to us and depending on their time in business we will ask for the following items

Companies that have been in business for more than two years we have a credit application program up to 250K . With this program we need the following items Credit application filled out(which is what I would like to be able for the customer to click on my website to get.) as well as three current month bank statements.

Deals over 250k we will need the following items

2 years business tax returns
2 years personal tax returns
Profit & Loss statement
Personal Financial Statement

what we do
100% FINANCING
SEASONAL PAYMENTS
LOAN BALLOON PAYMENTS
TRAC LEASING
LOW-INTEREST REFINANCING RATES
DEBT CONSOLIDATION

We specialize in creative financing solutions and offer a variety of reliable, flexible and expandable lending choices.

Target Market(s)

Trucking Companies

Industry/Entity Type

Trucking Company

Contact Information for Business Card

* $250,000 Application only Program
* Loans from $30,000 to 5,000,000
* Competitive Interest Rates

Font styles to use
Serif
Sans Serif

Colors

Designer to choose colors to be used in the design.

Requirements
Must have
• On the back of the card.
• * $250,000 Application only Program
• * Loans from $30,000 to 5,000,000
• My name, email, website. address
• * Competitive Interest Rates
• * 100% Financing
Nice to have
• I want my logo to pop on the card
• My logo is the great one I would like to use
Should not have
• I am up for your creativity as well

```html
<!DOCTYPE html>
<html lang="en">
<head>
<meta charset="UTF-8">
<title>Ridgeway Finance – Business Card</title>
<link href="https://fonts.googleapis.com/css2?family=Montserrat:wght@400;500;600;800&display=swap" rel="stylesheet">
<style>
  :root {
    --navy: #1b2a63;
    --navy-deep: #15204f;
    --red: #d51f34;
    --white: #ffffff;
    --paper: #f4f5f8;
    --mist: #e3e5ee;
    --stage: #d9dbe1;
    --silver: #c9ccd6;
  }
  * { margin: 0; padding: 0; box-sizing: border-box; }
  html, body { width: 1200px; height: 900px; overflow: hidden; }
  body {
    background: var(--stage);
    font-family: "Montserrat", sans-serif;
    display: flex;
    flex-direction: column;
    align-items: center;
    justify-content: center;
    gap: 28px;
  }
  .card {
    position: relative;
    width: 720px;
    height: 411px;
    border-radius: 22px;
    overflow: hidden;
    box-shadow: 0 10px 24px rgba(0,0,0,0.18);
  }

  /* Shared brand lockup */
  .brand { display: flex; align-items: center; gap: 14px; }
  .brand__dot { border-radius: 50%; flex: none; }
  .brand__name {
    font-weight: 800;
    text-transform: uppercase;
    letter-spacing: 0.02em;
    line-height: 1;
    white-space: nowrap;
  }

  /* Front */
  .card--front { background: linear-gradient(135deg, var(--white) 0%, var(--paper) 100%); }
  .card--front .brand { position: absolute; left: 48px; top: 48px; }
  .card--front .brand__dot { width: 46px; height: 46px; background: var(--navy); }
  .card--front .brand__name { font-size: 28px; color: var(--navy); }

  .watermark {
    position: absolute;
    right: 60px;
    top: 100px;
    width: 290px;
    height: 290px;
    border-radius: 50%;
    background: radial-gradient(circle, var(--mist) 0%, rgba(227,229,238,0.4) 70%, rgba(227,229,238,0) 100%);
  }

  .person {
    position: absolute;
    right: 48px;
    top: 160px;
    text-align: right;
  }
  .person__name {
    font-size: 28px;
    font-weight: 600;
    color: var(--red);
    text-transform: uppercase;
    letter-spacing: 0.02em;
    line-height: 1.1;
  }
  .person__role {
    margin-top: 6px;
    font-size: 16px;
    font-weight: 500;
    color: var(--navy);
  }

  .divider {
    position: absolute;
    left: 48px;
    right: 48px;
    top: 234px;
    height: 2px;
    background: var(--navy);
  }

  .contacts {
    position: absolute;
    left: 48px;
    top: 258px;
    list-style: none;
    display: flex;
    flex-direction: column;
    gap: 10px;
    font-size: 16px;
    font-weight: 500;
    color: var(--navy);
  }
  .contacts li { display: flex; align-items: center; gap: 10px; }
  .contacts svg { width: 14px; height: 14px; flex: none; }
  .contacts .accent { color: var(--red); }

  .address {
    position: absolute;
    right: 48px;
    top: 258px;
    text-align: right;
    font-size: 17px;
    font-weight: 500;
    font-style: normal;
    color: var(--navy);
    line-height: 1.5;
  }

  /* Back */
  .card--back {
    background: linear-gradient(135deg, var(--navy) 0%, var(--navy-deep) 100%);
    display: flex;
    flex-direction: column;
    align-items: center;
    justify-content: center;
    gap: 34px;
  }
  .card--back .brand { gap: 20px; }
  .card--back .brand__dot { width: 72px; height: 72px; background: var(--white); }
  .card--back .brand__name { font-size: 42px; color: var(--white); }

  .offers {
    list-style: none;
    display: grid;
    grid-template-columns: auto auto;
    column-gap: 44px;
    row-gap: 12px;
    font-size: 16px;
    font-weight: 500;
    color: var(--white);
  }
  .offers li { display: flex; align-items: center; gap: 10px; white-space: nowrap; }
  .offers li::before {
    content: "";
    width: 8px;
    height: 8px;
    background: var(--red);
    border-radius: 50%;
    flex: none;
  }
</style>
</head>
<body>
  <section class="card card--front" aria-label="Card front">
    <div class="watermark" role="img" aria-label="Faint large brand emblem in pale grey"></div>

    <div class="brand">
      <span class="brand__dot"></span>
      <span class="brand__name">Ridgeway Finance</span>
    </div>

    <div class="person">
      <div class="person__name">Daniel Harper</div>
      <div class="person__role">Director</div>
    </div>

    <div class="divider"></div>

    <ul class="contacts">
      <li>
        <svg viewBox="0 0 16 16" aria-hidden="true"><path d="M4 1.5l2.2 3-1.3 1.6c.8 1.8 2.2 3.2 4 4l1.6-1.3 3 2.2-1.3 2.5C7 13.5 2.5 9 1.5 3z" fill="var(--red)"/></svg>
        1300 555 014
      </li>
      <li>
        <svg viewBox="0 0 16 16" aria-hidden="true"><rect x="1.5" y="3.5" width="13" height="9" rx="1" fill="none" stroke="var(--red)" stroke-width="1.5"/><path d="M2 4l6 5 6-5" fill="none" stroke="var(--red)" stroke-width="1.5"/></svg>
        info@ridgewayfinance.com
      </li>
      <li>
        <svg viewBox="0 0 16 16" aria-hidden="true"><circle cx="8" cy="8" r="6.3" fill="none" stroke="var(--red)" stroke-width="1.4"/><path d="M1.8 8h12.4M8 1.7c-3 3.5-3 9.1 0 12.6M8 1.7c3 3.5 3 9.1 0 12.6" fill="none" stroke="var(--red)" stroke-width="1.2"/></svg>
        <span>www.<span class="accent">ridgewayfinance</span>.com</span>
      </li>
    </ul>

    <address class="address">
      2180 Maple Crest Dr.<br>
      Allen, TX 75013
    </address>
  </section>

  <section class="card card--back" aria-label="Card back">
    <div class="brand">
      <span class="brand__dot"></span>
      <span class="brand__name">Ridgeway Finance</span>
    </div>
    <ul class="offers">
      <li>$250,000 Application Only Program</li>
      <li>Competitive Interest Rates</li>
      <li>Loans from $30,000 to $5,000,000</li>
      <li>100% Financing</li>
    </ul>
  </section>
</body>
</html>
```